Chilli Jam Range. Label refresh.

We are expanding the Dunmore’s Pantry condiment family with a bold new Chilli Jam range. This collection celebrates vibrant, spicy flavours crafted for the gourmet market. The range includes five chilli jams and one crunchy chilli oil.
We are also refreshing the label design for this range. We want to retain key brand elements so that existing customers can still easily identify Dunmore’s Pantry products on the shelf.

Label Details
Jar Size: All products: 250ml tall glass jar 135mm tall x 60mm diameter.
Label Orientation: wraparound preferred but can be two set front/back.
Mandatory Inclusions:
Dunmore’s Pantry logo (retain existing or refreshed version)
Product name (see list below)
Net weight: 250ml
Barcode
Nutrition panel
Ingredients list
Country of Origin Statement.
Allergen Advisory.
Use/storage instructions (we’ll supply)
Business name and address

I would like one label that i can overprint BLACK (only) onto. As flavours can change through the season. Label should be able to represent all of the products listed below.
Range includes:
Classic Chilli Jam
Green Chilli Jam
Smoky Chipotle Chilli Jam
Pineapple Habanero Chilli Jam
Chilli Roasted Garlic Jam
Crunchy Chilli Oil

Target Market(s)

People who like chilli. Gourmet foodies. People buying gifts.

Industry/Entity Type

Gourmet food. Gift shops. Delicatessen

Colors
F0912C
F2A743
F7CA91
FBE8D2
FDF5EE
EE7325
F08F49
F5BC92
FAE3D3
FDF4ED
EB3D1F
EC4F4E
F09395
F8D3D4
FCEDEE

Requirements
Must have
• Create a label that we can overprint on. We over print in black ink only. One label for 6 chilli flavours.
Nice to have
• Brand recognition: Retain key identifiers from the existing Dunmore’s Pantry labels . Balancing traditional charm with a contemporary gourmet feel. Shelf impact: Use rich, vibrant colour palettes and bold typography to create standout in gourmet and gift settings.

```html
<!DOCTYPE html>
<html lang="en">
<head>
<meta charset="utf-8">
<title>Dunmore’s Pantry – Original Chilli Jam Label</title>
<link rel="stylesheet" href="https://fonts.googleapis.com/css2?family=Josefin+Sans:wght@600;700&family=Sacramento&display=swap">
<style>
  :root {
    --page: #f4efe9;
    --band-red: #d63b2b;
    --panel-orange: #e98a5e;
    --panel-glow: #f0a072;
    --cream-rule: #f6dfc4;
    --ink: #231f1c;
    --chilli-red: #e1372a;
    --chilli-deep: #c42a21;
  }
  * { margin: 0; padding: 0; box-sizing: border-box; }
  html, body {
    width: 1200px; height: 2422px; overflow: hidden;
    background: var(--page);
  }
  .label {
    position: absolute; left: 60px; top: 620px;
    width: 1080px; height: 1250px;
    font-family: "Josefin Sans", sans-serif;
    color: var(--ink);
    overflow: hidden;
  }
  .band {
    position: absolute; left: 0; width: 100%; height: 120px;
    background: var(--band-red);
    display: flex; align-items: center;
    font-weight: 700; letter-spacing: 8px; text-transform: uppercase;
  }
  .band--top { top: 0; justify-content: space-between; padding: 0 60px; font-size: 30px; }
  .band--bottom { bottom: 0; justify-content: center; font-size: 38px; letter-spacing: 9px; }
  .rule { position: absolute; left: 0; width: 100%; height: 8px; background: var(--cream-rule); }
  .rule--top { top: 120px; }
  .rule--bottom { bottom: 120px; }
  .panel {
    position: absolute; left: 0; top: 128px; width: 100%; height: 994px;
    background: radial-gradient(ellipse at 30% 40%, var(--panel-glow), var(--panel-orange) 70%);
  }
  .chilli-art {
    position: absolute; left: -120px; top: 360px;
    width: 560px; height: 560px;
    border-radius: 55% 45% 60% 40% / 40% 60% 40% 60%;
    background: linear-gradient(140deg, var(--chilli-red), var(--chilli-deep));
    transform: rotate(-20deg);
  }
  .chilli-slice {
    position: absolute; right: -60px; top: 270px;
    width: 220px; height: 170px;
    border-radius: 50%;
    background: linear-gradient(160deg, var(--chilli-red), var(--chilli-deep));
  }
  .brand {
    position: absolute; left: 0; top: 130px; width: 100%;
    display: flex; justify-content: center; align-items: center; gap: 26px;
  }
  .brand__mark { width: 46px; height: 46px; background: var(--ink); }
  .brand__name {
    font-size: 64px; font-weight: 700; letter-spacing: 10px;
    line-height: 1.1; text-transform: uppercase; color: var(--ink);
  }
  .product {
    position: absolute; left: 0; width: 100%; text-align: center;
  }
  .product__variant {
    top: 420px; font-family: "Sacramento", cursive;
    font-size: 150px; line-height: 1;
  }
  .product__name {
    top: 585px; font-size: 150px; font-weight: 700;
    line-height: 1; letter-spacing: 2px;
  }
  .product__tagline {
    top: 785px; font-size: 46px; font-weight: 700;
    letter-spacing: 5px; line-height: 1.55; text-transform: uppercase;
  }
  .product__flavour {
    top: 925px; font-family: "Sacramento", cursive;
    font-size: 100px; line-height: 1;
  }
  .net-volume {
    position: absolute; right: 40px; top: 1070px;
    font-size: 30px; font-weight: 600;
  }
</style>
</head>
<body>
  <main class="label">
    <div class="band band--top"><span>Australia</span><span>Proudly</span></div>
    <div class="rule rule--top"></div>
    <section class="panel">
      <div class="chilli-art" role="img" aria-label="Illustration of a long red chilli"></div>
      <div class="chilli-slice" role="img" aria-label="Illustration of a sliced chilli with seeds"></div>
    </section>
    <div class="brand">
      <span class="brand__mark"></span>
      <span class="brand__name">Dunmore’s<br>Pantry</span>
    </div>
    <p class="product product__variant">Original</p>
    <h1 class="product product__name">CHILLI JAM</h1>
    <p class="product product__tagline">A roaring blend of<br>chilli &amp; exotic spices</p>
    <p class="product product__flavour">Rich &amp; fiery</p>
    <span class="net-volume">250ml</span>
    <div class="rule rule--bottom"></div>
    <div class="band band--bottom">Made in small batches</div>
  </main>
</body>
</html>
```